Taro Reserve website (www.taroreserve.com)

My company develops booking software, Taro Reserve, for the hourly booking of resources such as classes in a school or customer booking involving rooms in a spa. These bookings also involve the customers, staff, rooms and a lesson or treatment.

The main difference between this software and general calendar software such as Plonkit calendar is that this Taro Reserve allows resources such as people and rooms to be associated with the bookings. This is important for example in the case of a Spa to make sure the rooms are booked appropriately and to see the free times for the rooms. For a golf practice range the players much be booked to the tee spots where they practice golf.

I have tried to design the website myself, as a computer programmer- I am a bit "square" and not a designer, my first attempt is http://www.taroreserve.com/, my second attempt is at http://www.lumex-works.com/taroreservewebsite/
I am not happy with my designs as compared to the professional designs I see people can come up with here. The software must have the image of a professional software product in order to inspire the confidence of customers.

Am looking for a design which will be the most likely to give the customer the following feeling:
* Confident the product can do the job.
* Feel easy to want to try it, at least for the free trial.
* Its a professional software product and also a web based product, the user can login from the web.

Look at other booking software websites for ideas, here is a list of links to similar booking products. These products all have different features but are mostly for resource booking.
http://lumex-works.com/taroreservewebsite/?page=compare
Updates

Hello all,

Thankyou for the designs so far, to save peoples time, I will try to eliminate the bottom 50% of designs now.

To be honest, most of the designs are of a good or high quality, I think its very tough on you as graphic and web designers. Only a minor few are of low quality.

If your design is discarded - I would say its unlikely that you are going to be able to produce a design that will beat the competition. 
You probably already know, you could try to re-sell your design later for other projects or as a template on one of those template websites. Some of these discarded designs are quite worthwhile designs.

Best regards, Gordon

Target Market(s)

Spa, Gym, School, Golf, any organization who manages bookings of their customers

Industry/Entity Type

Software

Requirements
Must have
• Home page and inner page, any other pages up to you.

Make a logo or use the image of the girl that I already have on the second design.

Menu(s) for navigation.

A language switcher for 3 languages, English, Chinese Traditional and Chinese Simplified. (Western, Hong Kong and Chinese mainland market are important).

Space for a video introduction, it could be small and when the user clicks on it then it gets bigger then it won't take up too much space. Up to you.

A space for the user to login and register a new account.

Screenshots.

I don't have any strong preferences, use your own ideas, if you look at all the other products you can get the basic idea from them.

The total goal is to make a website which is going to lead to sales of the software product.

```html
<!DOCTYPE html>
<html lang="en">
<head>
<meta charset="utf-8">
<title>Taro Reserve – Front Office Booking Software</title>
<link href="https://fonts.googleapis.com/css2?family=Ubuntu:ital,wght@0,300;0,400;0,500;0,700;1,300;1,400&display=swap" rel="stylesheet">
<style>
:root{
  --header-bg:#303235;
  --header-band:#3a3c40;
  --nav-bg:#3f4145;
  --nav-line:#2a2b2e;
  --accent:#e0502a;
  --light-band:#efefef;
  --step-bg:#f7f7f7;
  --step-line:#cfcfcf;
  --step-text:#8a8a8a;
  --quote-text:#a9a9a9;
  --content-bg:#49494c;
  --content-text:#e2e2e2;
  --rule:#d8d8d8;
  --footer-bg:#323335;
  --footer-text:#c9c9c9;
  --white:#ffffff;
}
*{box-sizing:border-box;margin:0;padding:0}
html,body{width:1200px;height:900px;overflow:hidden}
body{font-family:"Ubuntu",sans-serif;background:var(--content-bg);position:relative;color:var(--content-text)}
.site-header{position:absolute;left:0;top:0;width:1200px;height:185px;background:var(--header-bg)}
.brand-band{position:absolute;left:0;top:35px;width:720px;height:76px;background:linear-gradient(90deg,var(--header-band),var(--header-bg))}
.brand-name{position:absolute;left:59px;top:53px;font-size:40px;font-weight:400;color:var(--white);letter-spacing:1px}
.language-switch{position:absolute;right:20px;top:13px;display:flex;align-items:center;gap:8px;font-size:12px;color:#ddd}
.language-switch .option{display:flex;align-items:center;gap:4px}
.radio{width:14px;height:14px;border-radius:50%;background:#eee;border:1px solid #999;position:relative}
.radio.on::after{content:"";position:absolute;left:3px;top:3px;width:6px;height:6px;border-radius:50%;background:#333}
.account-btn{position:absolute;top:67px;height:35px;border-radius:4px;background:linear-gradient(#4c4f54,#383a3e);border:1px solid #25262a;color:#cfd6dd;font-size:15px;font-weight:500;display:flex;align-items:center;justify-content:center}
.btn-login{left:1010px;width:71px}
.btn-register{left:1097px;width:80px}
.main-nav{position:absolute;left:136px;top:143px;height:42px;display:flex}
.main-nav a{height:42px;display:flex;align-items:center;justify-content:center;color:var(--white);font-size:15px;font-weight:500;text-decoration:none;background:linear-gradient(#46484c,#393b3f);border-right:1px solid var(--nav-line)}
.main-nav a.current{border-top:4px solid var(--accent)}
.search-box{position:absolute;left:1028px;top:144px;width:160px;height:35px;border-radius:18px;background:#26282b;display:flex;align-items:center;padding-left:16px;gap:8px;color:#9aa0a6;font-size:14px}
.process-band{position:absolute;left:0;top:185px;width:1200px;height:211px;background:var(--light-band);border-bottom:2px solid #d5d5d5}
.tagline{position:absolute;left:82px;top:46px;font-size:20px;font-weight:700;color:var(--quote-text);line-height:23px}
.quote-mark{position:absolute;font-size:44px;font-weight:700;color:#c9c9c9;line-height:1}
.step-icon{position:absolute;top:32px;width:92px;height:88px;border-radius:8px}
.step-bar{position:absolute;left:13px;top:151px;width:1174px;height:48px}
.step-label{position:absolute;top:167px;font-size:14px;color:var(--step-text);transform:translateX(-50%)}
.about{position:absolute;left:135px;top:415px;width:470px}
.section-title{font-size:15.5px;font-weight:500;color:var(--white);padding-bottom:14px;border-bottom:1px solid var(--rule)}
.about .section-title{width:370px}
.body-copy{font-size:13.5px;font-weight:300;line-height:20px;margin-top:22px}
.industry-list{list-style:none;margin-top:2px}
.industry-list li{font-size:13.5px;font-weight:500;line-height:20px;display:flex;align-items:center;gap:6px}
.industry-list li::before{content:"";width:12px;height:12px;border-radius:50%;background:#e9e9e9}
.column-divider{position:absolute;left:711px;top:422px;width:1px;height:373px;background:var(--rule)}
.side{position:absolute;left:762px;top:415px;width:371px}
.video-thumb{position:absolute;left:0;top:60px;width:158px;height:118px;border-radius:6px;background:#f3f3f3;padding:5px}
.video-screen{width:100%;height:100%;background:#111;border-radius:3px;position:relative}
.video-text{position:absolute;left:186px;top:62px;width:185px;font-size:13.5px;font-weight:300;line-height:20px}
.feedback-block{position:absolute;left:0;top:201px;width:371px;border-top:1px solid var(--rule);padding-top:26px}
.testimonial{font-size:13px;font-style:italic;font-weight:300;line-height:16px;margin:0 0 18px 6px}
.site-footer{position:absolute;left:0;top:847px;width:1200px;height:53px;background:var(--footer-bg);display:flex;align-items:center;font-size:11px;color:var(--footer-text)}
.social{position:absolute;left:22px;display:flex;align-items:center;gap:9px;font-weight:500;color:var(--white)}
.social .square{width:20px;height:20px;background:#5a6fa8;border-radius:2px}
.footer-links{position:absolute;left:222px;display:flex;gap:0}
.footer-links a{color:var(--footer-text);text-decoration:none;font-weight:500}
.copyright{position:absolute;right:22px;color:#9a9a9a}
</style>
</head>
<body>
<header class="site-header">
  <div class="brand-band"></div>
  <div class="brand-name">Taro Reserve</div>
  <div class="language-switch">
    <span>Language:</span>
    <span class="option"><span class="radio on"></span>English</span>
    <span class="option"><span class="radio"></span>简体</span>
    <span class="option"><span class="radio"></span>繁體</span>
  </div>
  <a class="account-btn btn-login">Login</a>
  <a class="account-btn btn-register">Register</a>
  <nav class="main-nav">
    <a class="current" style="width:97px">Home</a>
    <a style="width:113px">Bookings</a>
    <a style="width:103px">Free Trial</a>
    <a style="width:137px">Documentation</a>
    <a style="width:109px">Compare</a>
    <a style="width:107px">Feedback</a>
    <a style="width:104px">Purchase</a>
    <a style="width:111px">Contact</a>
  </nav>
  <div class="search-box">
    <svg width="15" height="15" viewBox="0 0 15 15"><circle cx="6" cy="6" r="4.5" fill="none" stroke="#9aa0a6" stroke-width="2"/><line x1="9.5" y1="9.5" x2="14" y2="14" stroke="#9aa0a6" stroke-width="2"/></svg>
    <span>Search</span>
  </div>
</header>

<section class="process-band">
  <span class="quote-mark" style="left:44px;top:40px">“</span>
  <p class="tagline">Bookings have<br>never been<br>this easy...</p>
  <span class="quote-mark" style="left:196px;top:86px">”</span>
  <div class="step-icon" role="img" aria-label="Client details card icon" style="left:303px;background:linear-gradient(#f4f4f4,#d9ddd6)"></div>
  <div class="step-icon" role="img" aria-label="Clock icon" style="left:517px;border-radius:50%;background:radial-gradient(#fafafa,#b9b9b9)"></div>
  <div class="step-icon" role="img" aria-label="Calendar icon" style="left:737px;background:linear-gradient(#7cbf3c 0 24%,#eaeaea 24%)"></div>
  <div class="step-icon" role="img" aria-label="Envelope icon" style="left:969px;background:linear-gradient(#fbfbfb,#dedede)"></div>
  <svg class="step-bar" viewBox="0 0 1174 48">
    <rect x="0.5" y="0.5" width="1173" height="47" rx="4" fill="#f8f8f8" stroke="#cfcfcf"/>
    <path d="M432 1 L454 24 L432 47 M661 1 L683 24 L661 47 M878 1 L900 24 L878 47" fill="none" stroke="#cfcfcf"/>
  </svg>
  <span class="step-label" style="left:340px">1. Client Details</span>
  <span class="step-label" style="left:568px">2. Set Date &amp; Time</span>
  <span class="step-label" style="left:790px">3. Schedule</span>
  <span class="step-label" style="left:1020px">4. Confirm / Email</span>
</section>

<main>
  <section class="about">
    <h2 class="section-title">About Taro Reserve</h2>
    <p class="body-copy">Taro Reserve is a front office booking software which makes managing bookings, rooms and staff availability fast and simple.&nbsp; We focus on producing the best quality software that is powerful yet easy to use.</p>
    <p class="body-copy" style="margin-top:20px">Taro Reserve is suitable for various industries including:</p>
    <ul class="industry-list">
      <li>Salons / Spas</li>
      <li>Sport / Recreational Facilities</li>
      <li>Schools</li>
      <li>Healthcare</li>
      <li>Event Planners</li>
      <li>and many more</li>
    </ul>
    <p class="body-copy" style="margin-top:20px">Taro Reserve stores all data on our servers in the SaaS model giving<br>a very low total cost of ownership our customers.</p>
    <p class="body-copy" style="margin-top:20px">You have zero investment in: server platform hardware, software licenses, hardware and software upgrades.&nbsp; All are included as part of our service.</p>
  </section>

  <div class="column-divider"></div>

  <aside class="side">
    <h2 class="section-title">Take a Video Tour</h2>
    <div class="video-thumb">
      <div class="video-screen">
        <svg width="148" height="108" viewBox="0 0 148 108" style="position:absolute;left:0;top:0">
          <rect x="52" y="30" width="44" height="34" rx="6" fill="#2c2c2c" stroke="#555"/>
          <path d="M67 38 L82 47 L67 56 Z" fill="#fff"/>
          <rect x="6" y="96" width="136" height="3" fill="#c0281e"/>
        </svg>
      </div>
    </div>
    <p class="video-text">This video tour explains how Taro Reserve can improve your company’s scheduling and time management with ease.</p>
    <div class="feedback-block">
      <h2 class="section-title" style="margin-bottom:22px">Client Feedback</h2>
      <p class="testimonial">“An exceptional product that works for me &amp; my clients”<br>- The Calm Rooms Group</p>
      <p class="testimonial">“Managaing classes has never been so easy”<br>- University of Norvale</p>
      <p class="testimonial">“Amazing! It’s like a diary that alerts me on time”<br>- Brightwell Events</p>
    </div>
  </aside>
</main>

<footer class="site-footer">
  <div class="social"><span class="square"></span>Join Us on Chatterly</div>
  <nav class="footer-links">
    <a style="margin-right:41px">About</a>
    <a style="margin-right:41px">Events</a>
    <a style="margin-right:41px">Press</a>
    <a style="margin-right:41px">Jobs</a>
    <a style="margin-right:41px">Staff</a>
    <a style="margin-right:41px">Resources</a>
    <a style="margin-right:41px">Privacy</a>
    <a style="margin-right:41px">T&amp;Cs</a>
    <a style="margin-right:41px">Feedback</a>
    <a style="margin-right:41px">Customer Service</a>
    <a>Contact</a>
  </nav>
  <span class="copyright">© 2011 Taro Reserve</span>
</footer>
</body>
</html>
```